Tall Fern Roofing Business Card

Need a business card with the logo that was designed here

Contact Information for Business Card

Name, Title, Phone, Email, Website, Company name

```html
<!DOCTYPE html>
<html lang="en">
<head>
<meta charset="UTF-8">
<title>Tall Fern Roofing Business Card</title>
<link rel="stylesheet" href="https://fonts.googleapis.com/css2?family=Open+Sans:wght@400;600;700;800&display=swap">
<style>
  :root {
    --brand-blue: #1c75bc;
    --brand-grey: #939598;
    --ink: #2b2b2b;
    --paper: #ffffff;
    --backdrop: #4a4a4a;
  }
  * { box-sizing: border-box; margin: 0; padding: 0; }
  html, body {
    width: 1200px; height: 801px; overflow: hidden;
    background: var(--backdrop);
    font-family: "Open Sans", Arial, sans-serif;
  }
  .sheet {
    width: 1200px; height: 801px;
    display: flex; align-items: center; justify-content: center; gap: 40px;
  }
  .card {
    position: relative; width: 540px; height: 309px;
    border-radius: 18px; overflow: hidden;
  }
  .card--front { background: var(--paper); }
  .card--back { background: var(--brand-blue); display: flex; align-items: center; justify-content: center; }
  .wave { position: absolute; inset: 0; width: 100%; height: 100%; }
  .wordmark { display: flex; align-items: center; gap: 10px; font-weight: 700; white-space: nowrap; }
  .wordmark__mark { display: block; }
  .card--front .wordmark {
    position: absolute; left: 32px; top: 112px;
    color: var(--brand-blue); font-size: 23px;
  }
  .card--front .wordmark__mark { width: 14px; height: 14px; background: var(--brand-blue); }
  .card--back .wordmark { color: var(--paper); font-size: 42px; gap: 14px; }
  .card--back .wordmark__mark { width: 24px; height: 24px; background: var(--paper); }
  .divider {
    position: absolute; left: 280px; top: 42px; width: 1.5px; height: 165px;
    background: var(--brand-blue);
  }
  .contact { position: absolute; left: 298px; top: 34px; color: var(--ink); }
  .contact__name { color: var(--brand-blue); font-size: 21px; font-weight: 800; letter-spacing: 0.5px; line-height: 1.1; }
  .contact__title { font-size: 12px; margin-bottom: 12px; }
  .contact__address { font-size: 12.5px; line-height: 1.35; margin-bottom: 10px; }
  .contact__list { list-style: none; font-size: 12.5px; line-height: 1.45; }
  .contact__list li { display: flex; align-items: center; gap: 6px; }
  .contact__list svg { width: 11px; height: 11px; flex: none; }
</style>
</head>
<body>
<main class="sheet">
  <section class="card card--front" aria-label="Card front">
    <svg class="wave" viewBox="0 0 540 309" preserveAspectRatio="none" aria-hidden="true">
      <path d="M0 262 C190 262 340 230 430 180 C480 152 515 137 540 133" fill="none" stroke="var(--brand-grey)" stroke-width="3"/>
      <path d="M0 309 V284 C180 285 340 255 430 200 C480 172 515 158 540 155 V309 Z" fill="var(--brand-blue)"/>
      <path d="M70 300 C230 290 360 255 450 205" fill="none" stroke="var(--paper)" stroke-width="1.6"/>
    </svg>
    <div class="wordmark"><span class="wordmark__mark"></span>Tall Fern Roofing</div>
    <div class="divider"></div>
    <div class="contact">
      <h1 class="contact__name">DANA WHITLOW</h1>
      <p class="contact__title">Managing Director</p>
      <p class="contact__address">Your address, City<br>State, Zip 1234</p>
      <ul class="contact__list">
        <li><svg viewBox="0 0 12 12"><path d="M2.5 1 L4.5 1 L5.2 3.5 L4 4.5 C4.6 6 6 7.4 7.5 8 L8.5 6.8 L11 7.5 L11 9.5 C11 10.3 10.3 11 9.5 11 C5 11 1 7 1 2.5 C1 1.7 1.7 1 2.5 1 Z" fill="var(--brand-blue)"/></svg>123 456 789</li>
        <li><svg viewBox="0 0 12 12"><rect x="1" y="2.5" width="10" height="7" rx="1" fill="var(--brand-blue)"/><path d="M1.5 3 L6 6.5 L10.5 3" fill="none" stroke="var(--paper)" stroke-width="1"/></svg>info@yourgmail.com</li>
        <li><svg viewBox="0 0 12 12"><circle cx="6" cy="6" r="5" fill="var(--brand-blue)"/><path d="M1 6 H11 M6 1 C3.5 3.5 3.5 8.5 6 11 M6 1 C8.5 3.5 8.5 8.5 6 11" fill="none" stroke="var(--paper)" stroke-width="0.8"/></svg>www.yourwebsite.com</li>
      </ul>
    </div>
  </section>
  <section class="card card--back" aria-label="Card back">
    <div class="wordmark"><span class="wordmark__mark"></span>Tall Fern Roofing</div>
  </section>
</main>
</body>
</html>
```